Informational Site for Advanced Chemistry R&D

The company develops oxidation chemistry for air, water, fuel pollution controls. The site has been prototyped at www.velquaresearch.example. Take a look. Now, the task is to design it for eye-catching beauty with use of color, on-page scroll-driven color transition and parallax effects. Should capture the themes: high technology, wow it's beautiful, modern, uncluttered, clean urban environment.

Target Market(s)

China Environmentally Conscious Government and Industry,

Industry/Entity Type

It Company

Number of Pages Required

3 page

Font styles to use
Sans Serif

Requirements
Must have
• Parallax effects, desktop compatible, Rich, Modern, Simple, Graphic
Nice to have
• Mobile Phone Compatible
Should not have
• Flash, or anything that is slow to load or requires high bandwidth

```html
<!DOCTYPE html>
<html lang="en">
<head>
<meta charset="utf-8">
<title>Velqura Science — Advanced Oxidation Science</title>
<link href="https://fonts.googleapis.com/css2?family=Jost:wght@300;400;500&family=Open+Sans:wght@400;600;700&display=swap" rel="stylesheet">
<style>
:root{
  --blue:#1b6fb5;
  --blue-dark:#14518a;
  --teal:#2aa3cc;
  --ink:#2b2b2b;
  --muted:#555;
  --grey-band:#f1f1f1;
  --night:#1c3550;
  --night-deep:#0f2236;
  --white:#fff;
  --line:#e3e3e3;
}
*{box-sizing:border-box;margin:0;padding:0}
html,body{width:1200px;height:3321px;overflow:hidden}
body{position:relative;background:var(--white);font-family:'Open Sans',Arial,sans-serif;color:var(--ink)}
.abs{position:absolute}
h2.section-title{position:absolute;left:0;width:1200px;text-align:center;font-family:'Jost',Arial,sans-serif;font-weight:300;font-size:40px;color:var(--ink)}
.accent{color:var(--teal)}
.btn{position:absolute;display:flex;align-items:center;justify-content:center;background:var(--blue);color:var(--white);font-size:14px;border-radius:3px}

/* header */
.site-header{left:0;top:0;width:1200px;height:155px;background:var(--white);border-top:4px solid var(--blue)}
.brand{left:122px;top:48px;display:flex;align-items:center;gap:12px;font-family:'Jost',Arial,sans-serif;font-weight:500;font-size:36px;color:var(--teal)}
.brand-dot{width:26px;height:26px;border-radius:50%;background:var(--teal)}
.phone{left:966px;top:52px;display:flex;align-items:center;gap:10px;font-size:14px;color:var(--ink)}
.nav{left:752px;top:92px;display:flex;gap:0;font-family:'Jost',Arial,sans-serif;font-size:15px}
.nav a{color:var(--ink);text-decoration:none;width:105px;text-align:center;position:relative}
.nav a.current{color:var(--blue)}
.nav a.current::after{content:"";position:absolute;left:32px;right:32px;top:26px;height:3px;border-radius:3px;background:var(--teal)}

/* hero */
.hero{left:0;top:155px;width:1200px;height:514px;background:linear-gradient(180deg,#5f7fa6 0%,#3d5a7e 40%,#2b3c52 62%,#4a5f78 80%,#22324a 100%)}
.hero-ring{left:556px;top:168px;width:88px;height:88px;border-radius:50%;border:5px solid var(--white)}
.hero-title{left:0;width:1200px;top:278px;text-align:center;font-family:'Jost',Arial,sans-serif;font-weight:400;font-size:34px;line-height:48px;color:var(--white)}
.hero-arrow{top:230px}

/* welcome */
.welcome-photo{left:100px;top:720px;width:380px;height:270px;border:6px solid var(--white);box-shadow:0 0 0 1px var(--line);background:linear-gradient(180deg,#3d86c8 0%,#8fb6d8 55%,#8a8a86 70%,#4d4d4a 100%)}
.welcome-title{left:505px;top:712px;font-family:'Jost',Arial,sans-serif;font-weight:300;font-size:38px}
.welcome-text{left:505px;top:770px;width:580px;font-size:12.5px;line-height:21px;color:var(--muted)}

/* solutions */
.solution-band{left:0;top:1047px;width:1200px;height:421px;background:var(--grey-band)}
.solution{width:300px;text-align:center}
.solution .disc{width:132px;height:132px;margin:0 auto;border-radius:50%;background:radial-gradient(circle at 40% 30%,#3a8fd3,var(--blue-dark));display:flex;align-items:center;justify-content:center}
.solution h3{font-family:'Jost',Arial,sans-serif;font-weight:400;font-size:21px;margin-top:22px}
.solution p{font-size:13.5px;line-height:24px;color:var(--muted);margin-top:6px;padding:0 14px}

/* oxidation */
.oxidation-figure{left:144px;top:1512px;width:361px;height:337px;background:radial-gradient(circle at 50% 45%,#fff6b8 0%,#fdf3c0 25%,#ffffff 60%)}
.oxidation-title{left:593px;top:1535px;font-family:'Jost',Arial,sans-serif;font-weight:300;font-size:38px}
.oxidation-text{left:597px;top:1600px;width:500px;font-size:13.5px;line-height:24px;color:var(--muted)}
.ticks{list-style:none;margin:4px 0 6px 26px}
.ticks li{display:flex;align-items:center;gap:10px}

/* products */
.product-band{left:0;top:1915px;width:1200px;height:288px;background:var(--grey-band)}
.product-card{top:2125px;width:234px;height:288px;background:var(--white);border:1px solid var(--line);text-align:center}
.product-card .thumb{position:absolute;left:37px;top:-78px;width:160px;height:160px;border-radius:50%;border:7px solid var(--white);box-shadow:0 0 0 2px #dcdcdc}
.product-card h3{position:absolute;top:96px;left:0;width:100%;font-family:'Jost',Arial,sans-serif;font-weight:400;font-size:16px}
.product-card p{position:absolute;top:124px;left:12px;right:12px;font-size:13px;line-height:20px;color:var(--muted);height:100px;overflow:hidden}
.product-card .btn{left:62px;top:236px;width:110px;height:38px;font-size:13px}

/* partners */
.partner{top:2573px;width:195px;height:133px;border:6px solid #f0f0f0;background:var(--white);display:flex;align-items:center;justify-content:center}
.partner .badge{width:78px;height:78px;border-radius:50%}
.partner .badge-name{font-family:'Jost',Arial,sans-serif;font-weight:500;font-size:17px;color:var(--blue)}

/* contact */
.contact{left:0;top:2759px;width:1200px;height:503px;background:linear-gradient(180deg,var(--night-deep) 0%,var(--night) 55%,#2b4a6b 75%,var(--night-deep) 100%)}
.contact-title{left:0;width:1200px;top:2792px;text-align:center;font-family:'Jost',Arial,sans-serif;font-weight:400;font-size:36px;color:var(--white)}
.map{left:100px;top:2867px;width:372px;height:335px;border:5px solid #c9c9c9;background:linear-gradient(135deg,#e8e3d6 0%,#d9dccf 50%,#e9e4d5 100%)}
.field{left:505px;width:372px;height:42px;background:var(--white);display:flex;align-items:center;gap:12px;padding-left:16px;font-size:13px;color:#8a8a8a}
.field.message{height:104px;align-items:flex-start;padding-top:12px}
.address{left:908px;top:2898px;color:var(--white)}
.address h4{font-family:'Open Sans',Arial,sans-serif;font-weight:700;font-size:19px;margin-bottom:16px}
.address .row{display:flex;gap:14px;font-size:13px;line-height:18px;margin-bottom:22px;width:230px}

/* footer */
.site-footer{left:0;top:3262px;width:1200px;height:59px;background:var(--blue);color:var(--white);font-size:12px}
.site-footer .copy{position:absolute;left:97px;top:21px}
.social{position:absolute;left:930px;top:14px;display:flex;gap:8px}
.social span{width:28px;height:28px;border-radius:50%;border:1.5px solid rgba(255,255,255,.8)}
.site-footer .code{position:absolute;left:1170px;top:21px}
</style>
</head>
<body>

<header class="abs site-header">
  <div class="abs brand"><span class="brand-dot"></span>Velqura</div>
  <div class="abs phone">
    <svg width="22" height="22" viewBox="0 0 22 22"><circle cx="11" cy="11" r="10" fill="none" stroke="#1b6fb5" stroke-width="1.5"/><path d="M7.5 6.5l2 -.5 1 2.5-1.3 1c.6 1.3 1.6 2.3 2.9 2.9l1-1.3 2.5 1-.5 2c-4.6-.3-7.3-3-7.6-7.6z" fill="#1b6fb5"/></svg>
    +1 555 010 4590
  </div>
  <nav class="abs nav"><a class="current">Home</a><a>Technology</a><a>Products</a><a>Contact</a></nav>
</header>

<section class="abs hero" role="img" aria-label="City skyline reflected in a river at dusk">
  <div class="abs hero-ring"></div>
  <svg class="abs hero-arrow" style="left:40px" width="22" height="60" viewBox="0 0 22 60"><path d="M18 2L4 30l14 28" fill="none" stroke="#fff" stroke-width="2" opacity=".7"/></svg>
  <svg class="abs hero-arrow" style="left:1138px" width="22" height="60" viewBox="0 0 22 60"><path d="M4 2l14 28L4 58" fill="none" stroke="#fff" stroke-width="2" opacity=".7"/></svg>
  <h1 class="abs hero-title">Advanced Oxidation Science for Environmental<br>Pollution Management</h1>
</section>

<section>
  <div class="abs welcome-photo" role="img" aria-label="Industrial plant with silo and pipework under a blue sky"></div>
  <h2 class="abs welcome-title">Welcome to <span class="accent">Velqura</span></h2>
  <p class="abs welcome-text">Velqura Science develops advanced oxidation technologies and materials, which it licenses to Velqura Systems, China. Velqura Systems is engaged in the sales, service and support of environmental solutions for industry and government. With offices in Shanghai, Beijing, Shijiazhuang, and Chengdu, Velqura Systems is among the most advanced and rapidly growing companies offering solutions for air, water and fuel environmental compliance. Velqura Science Corporation supports these solutions with research and development. Velqura Science Corporation pursues business development opportunities in markets worldwide.</p>
  <div class="btn" style="left:505px;top:950px;width:140px;height:42px">View more info</div>
</section>

<section>
  <div class="abs solution-band"></div>
  <h2 class="section-title" style="top:1090px">Our <span class="accent">Solution</span></h2>
  <div class="abs solution" style="left:115px;top:1166px">
    <div class="disc"><svg width="40" height="52" viewBox="0 0 40 52"><path d="M20 2C14 14 4 24 4 34a16 16 0 0 0 32 0C36 24 26 14 20 2z" fill="#fff"/></svg></div>
    <h3>Water</h3>
    <p>Our proprietary low temperature and pressure advanced oxidation catalytic process reliably removes sulfur from diesel</p>
  </div>
  <div class="abs solution" style="left:448px;top:1166px">
    <div class="disc"><svg width="56" height="44" viewBox="0 0 56 44" fill="none" stroke="#fff" stroke-width="3" stroke-linecap="round"><path d="M4 14h30a7 7 0 1 0-7-7"/><path d="M4 24h42a7 7 0 1 1-7 7"/><path d="M10 34h18"/></svg></div>
    <h3>Air</h3>
    <p>Our proprietary low temperature and pressure advanced oxidation catalytic process reliably removes sulfur from diesel</p>
  </div>
  <div class="abs solution" style="left:775px;top:1166px">
    <div class="disc"><svg width="44" height="54" viewBox="0 0 44 54"><path d="M22 2c4 10 16 18 16 32a16 16 0 0 1-32 0c0-7 4-12 8-16 0 6 3 9 6 9 0-10-2-16 2-25z" fill="#fff"/></svg></div>
    <h3>Fuel</h3>
    <p>Our proprietary low temperature and pressure advanced oxidation catalytic process reliably removes sulfur from diesel</p>
  </div>
</section>

<section>
  <div class="abs oxidation-figure" role="img" aria-label="Diagram of the hydroxyl radical reacting with surrounding pollutant molecules"></div>
  <h2 class="abs oxidation-title">Advanced <span class="accent">Oxidation</span></h2>
  <div class="abs oxidation-text">
    <p>Advanced Oxidation refers to a variety of techniques employing the Hydroxyl Radical, an energetic, highly reactive cousin of the water molecule:</p>
    <ul class="ticks">
      <li><svg width="12" height="10" viewBox="0 0 12 10"><path d="M1 5l3.5 3.5L11 1.5" fill="none" stroke="#2aa3cc" stroke-width="2"/></svg>To add oxygen to inorganic molecules</li>
      <li><svg width="12" height="10" viewBox="0 0 12 10"><path d="M1 5l3.5 3.5L11 1.5" fill="none" stroke="#2aa3cc" stroke-width="2"/></svg>To remove hydrogen from organic molecules</li>
    </ul>
    <p>These transformations convert important industrial contaminants into reactive forms that can be captured or that disintegrate into harmless end products.</p>
  </div>
  <div class="btn" style="left:597px;top:1808px;width:136px;height:44px">View more info</div>
</section>

<section>
  <div class="abs product-band"></div>
  <h2 class="section-title" style="top:1960px">Our <span class="accent">Products</span></h2>
  <article class="abs product-card" style="left:100px">
    <div class="thumb" role="img" aria-label="Refinery pipework" style="background:linear-gradient(160deg,#9ab4c8,#3f5366)"></div>
    <h3>Fuel Oil Desulfurization</h3>
    <p>Our proprietary low temperature and pressure advanced oxidation catalytic process reliably removes sulfur from diesel transportation fuel at half the operating</p>
    <div class="btn">View more</div>
  </article>
  <article class="abs product-card" style="left:354px">
    <div class="thumb" role="img" aria-label="Laboratory technician at work" style="background:linear-gradient(160deg,#c9d6e0,#4d6a8a)"></div>
    <h3>Volatile Organic Compunds</h3>
    <p>Alkanes, alkenes, halogenated hydrocarbons, aromatic hydro carbons, esters, aldehydes, polycyclic aromatic hydrocarbons, We convert these by-products.</p>
    <div class="btn">View more</div>
  </article>
  <article class="abs product-card" style="left:611px">
    <div class="thumb" role="img" aria-label="Industrial chimneys against a blue sky" style="background:linear-gradient(180deg,#4f7fb8,#1f2d3e)"></div>
    <h3>Fuel Oil Desulfurization</h3>
    <p>Desulfurization and denitrification using our proprietary flue gas advanced oxidation catalytic process (FGAOC). Sulfur and nitrogen are oxidized</p>
    <div class="btn">View more</div>
  </article>
  <article class="abs product-card" style="left:868px">
    <div class="thumb" role="img" aria-label="Wastewater outflow pipe" style="background:linear-gradient(180deg,#8a8f7a,#a67c46)"></div>
    <h3>Wastewater Treatment</h3>
    <p>Photoelectrocatalysed (PEC) anodic oxidation removes soluble organics. Novel anode design using our proprietary nano-carbon surface operates</p>
    <div class="btn">View more</div>
  </article>
</section>

<section>
  <h2 class="section-title" style="top:2500px">Our <span class="accent">Partners</span></h2>
  <div class="abs partner" style="left:133px"><span class="badge-name">Velqura Systems</span></div>
  <div class="abs partner" style="left:381px"><span class="badge" style="background:#e2742a"></span></div>
  <div class="abs partner" style="left:626px"><span class="badge" style="background:#2f5d9c"></span></div>
  <div class="abs partner" style="left:870px"><span class="badge" style="background:#b3262c"></span></div>
</section>

<section class="abs contact" role="img" aria-label="Night city skyline behind the contact area"></section>
<h2 class="abs contact-title">Contact us</h2>
<div class="abs map" role="img" aria-label="Street map showing the office location"></div>
<div class="abs field" style="top:2867px"><svg width="14" height="14" viewBox="0 0 14 14"><circle cx="7" cy="4" r="3.5" fill="#888"/><path d="M0 14c0-4 3-6 7-6s7 2 7 6z" fill="#888"/></svg>Your name</div>
<div class="abs field" style="top:2925px"><svg width="15" height="11" viewBox="0 0 15 11"><rect width="15" height="11" fill="#888"/><path d="M0 0l7.5 6L15 0" fill="none" stroke="#fff"/></svg>Email address</div>
<div class="abs field" style="top:2982px"><svg width="12" height="14" viewBox="0 0 12 14"><rect width="12" height="14" fill="#888"/></svg>Subject</div>
<div class="abs field message" style="top:3038px"><svg width="14" height="14" viewBox="0 0 14 14"><path d="M1 13l1-4 8-8 3 3-8 8z" fill="#888"/></svg>Message</div>
<div class="btn" style="left:505px;top:3160px;width:155px;height:44px;border-radius:0">Submit</div>
<div class="abs address">
  <h4>Contact Address</h4>
  <div class="row"><svg width="12" height="16" viewBox="0 0 12 16"><path d="M6 0a6 6 0 0 1 6 6c0 4-6 10-6 10S0 10 0 6a6 6 0 0 1 6-6z" fill="#fff"/><circle cx="6" cy="6" r="2" fill="#1c3550"/></svg><span>Velqura Science Corporation, Riverton, U.S.A</span></div>
  <div class="row"><svg width="14" height="14" viewBox="0 0 14 14"><path d="M1 2l3-1 2 3.5-2 1.5c1 2 2.5 3.5 4.5 4.5l1.5-2 3.5 2-1 3C6 13 1 8 1 2z" fill="#fff"/></svg><span style="font-size:15px">+1 555 010 6657</span></div>
  <div class="row"><svg width="15" height="11" viewBox="0 0 15 11"><rect width="15" height="11" fill="#fff"/><path d="M0 0l7.5 6L15 0" fill="none" stroke="#1c3550"/></svg><span>info@velquaresearch.example</span></div>
</div>

<footer class="abs site-footer">
  <span class="copy">Copyright 2016 velqura. All Rights Reserved</span>
  <div class="social"><span></span><span></span><span></span><span></span><span></span></div>
  <span class="code">C12</span>
</footer>

</body>
</html>
```